Business Card Design for Varomir Facility Services

We are looking for a Business Card Design for the Company "Varomir Facility Services."
Front side:
- Company Logo (small)
- Company Name, address, pohone, website and personal data.
- white background, for text e.g. company colors (blue or green like in the logo)
Please use following data:
Company data:
Varomir Facility Services Kostelac
Birkenhaldweg 14
6330 Cham
www.varomir-fs.ch
Person data:
Tarik Kostelac
Geschäftsführer
+41 76 519 47 83
info@varomir-fs.ch
Back side:
could be colored in blue or green
please use a big logo sing and some smaller icons to say what is all beeing offered in facility services, like cleaning, maintenance cleaning
industrial cleaning, caretaking, gardening, disposal. There is no need for everyone of the icons if there are similar or an icon is standing for more of them.
colors to use:
blue: HEX 246BB0
green: HEX 52B33E

```html
<!DOCTYPE html>
<html lang="de">
<head>
<meta charset="utf-8">
<title>Varomir Facility Services – Visitenkarte</title>
<link rel="stylesheet" href="https://fonts.googleapis.com/css2?family=Roboto:wght@400;500;700;900&display=swap">
<style>
  :root {
    --brand-blue: #246bb0;
    --brand-green: #52b33e;
    --ring-green: #1fa33a;
    --light-blue: #a9d4ff;
    --white: #ffffff;
    --stage: #e9e9ea;
  }
  * { box-sizing: border-box; margin: 0; padding: 0; }
  html, body { width: 1200px; height: 1200px; overflow: hidden; }
  body {
    background: var(--stage);
    font-family: "Roboto", Arial, sans-serif;
    position: relative;
  }
  .card {
    position: absolute;
    left: 120px;
    width: 960px;
    height: 540px;
    border-radius: 34px;
    overflow: hidden;
  }
  /* back side */
  .card-back { top: 40px; background: var(--brand-blue); color: var(--white); }
  .back-brand {
    position: absolute; top: 92px; left: 0; right: 0;
    display: flex; flex-direction: column; align-items: center; gap: 6px;
  }
  .back-brand .brand-mark {
    width: 58px; height: 58px; border-radius: 50%;
    border: 6px solid var(--white); margin-bottom: 14px;
  }
  .back-brand .brand-name {
    font-weight: 700; font-size: 104px; letter-spacing: 6px; line-height: 1;
    text-transform: uppercase;
  }
  .back-brand .brand-sub {
    font-weight: 700; font-size: 34px; letter-spacing: 12px; text-transform: uppercase;
  }
  .service-list {
    position: absolute; top: 350px; left: 0; right: 0;
    display: flex; justify-content: center; gap: 58px; list-style: none;
  }
  .service { display: flex; flex-direction: column; align-items: center; width: 130px; }
  .service-badge {
    width: 106px; height: 106px; border-radius: 50%;
    background: var(--white); padding: 6px;
  }
  .service-badge .ring {
    width: 100%; height: 100%; border-radius: 50%;
    border: 3px solid var(--brand-blue);
    display: flex; align-items: center; justify-content: center;
  }
  .service-icon { width: 52px; height: 52px; border-radius: 10px; background: var(--brand-blue); }
  .service-name {
    margin-top: 10px; font-weight: 900; font-size: 15px; text-align: center;
    text-transform: uppercase; line-height: 1.1;
  }
  /* front side */
  .card-front { top: 620px; background: var(--brand-blue); }
  .front-shape { position: absolute; inset: 0; }
  .front-brand {
    position: absolute; left: 40px; top: 168px; width: 420px;
    color: var(--brand-blue); display: flex; flex-direction: column; align-items: center;
  }
  .front-brand .brand-mark {
    width: 46px; height: 46px; border-radius: 50%;
    border: 6px solid var(--brand-blue); margin-bottom: 12px;
  }
  .front-brand .brand-name {
    font-weight: 700; font-size: 78px; letter-spacing: 4px; line-height: 1; text-transform: uppercase;
  }
  .front-brand .brand-sub {
    margin-top: 8px; font-weight: 700; font-size: 24px; letter-spacing: 7px; text-transform: uppercase;
    color: var(--brand-green);
  }
  .contact {
    position: absolute; left: 545px; top: 150px; color: var(--white);
  }
  .person-name { font-weight: 900; font-size: 34px; line-height: 1.1; }
  .person-role { font-size: 20px; margin-top: 2px; }
  .company-name { margin-top: 24px; font-weight: 700; font-size: 22px; color: var(--light-blue); }
  .address { font-size: 22px; line-height: 1.3; font-style: normal; }
  .contact-lines { list-style: none; margin-top: 6px; font-size: 22px; line-height: 1.45; }
  .contact-lines li { display: flex; align-items: center; gap: 10px; }
  .contact-lines svg { width: 20px; height: 20px; flex: none; }
  .contact-lines strong { font-weight: 700; }
</style>
</head>
<body>

<section class="card card-back" aria-label="Rückseite">
  <div class="back-brand">
    <span class="brand-mark" aria-hidden="true"></span>
    <span class="brand-name">Varomir</span>
    <span class="brand-sub">Facility Services</span>
  </div>
  <ul class="service-list">
    <li class="service">
      <div class="service-badge"><div class="ring"><span class="service-icon" role="img" aria-label="Symbol Reinigungsbürste"></span></div></div>
      <span class="service-name">Maintenance<br>Cleaning</span>
    </li>
    <li class="service">
      <div class="service-badge"><div class="ring"><span class="service-icon" role="img" aria-label="Symbol Handschlag im Herz"></span></div></div>
      <span class="service-name">Caretaking</span>
    </li>
    <li class="service">
      <div class="service-badge"><div class="ring"><span class="service-icon" role="img" aria-label="Symbol Blume im Topf"></span></div></div>
      <span class="service-name">Gardening</span>
    </li>
    <li class="service">
      <div class="service-badge"><div class="ring"><span class="service-icon" role="img" aria-label="Symbol Mülleimer"></span></div></div>
      <span class="service-name">Disposal</span>
    </li>
  </ul>
</section>

<section class="card card-front" aria-label="Vorderseite">
  <svg class="front-shape" viewBox="0 0 960 540" aria-hidden="true">
    <circle cx="170" cy="250" r="330" fill="var(--white)"/>
    <circle cx="170" cy="250" r="318" fill="none" stroke="var(--ring-green)" stroke-width="4"/>
  </svg>
  <div class="front-brand">
    <span class="brand-mark" aria-hidden="true"></span>
    <span class="brand-name">Varomir</span>
    <span class="brand-sub">Facility Services</span>
  </div>
  <div class="contact">
    <p class="person-name">Tarik Kostelac</p>
    <p class="person-role">Geschäftsführer</p>
    <p class="company-name">Varomir Facility Services Kostelac</p>
    <address class="address">Birkenhaldweg 14<br>6330 Cham</address>
    <ul class="contact-lines">
      <li>
        <svg viewBox="0 0 24 24"><path fill="var(--white)" d="M6.6 10.8a15 15 0 0 0 6.6 6.6l2.2-2.2a1 1 0 0 1 1-.25 11.4 11.4 0 0 0 3.6.57 1 1 0 0 1 1 1V20a1 1 0 0 1-1 1A17 17 0 0 1 3 4a1 1 0 0 1 1-1h3.5a1 1 0 0 1 1 1c0 1.25.2 2.45.57 3.57a1 1 0 0 1-.25 1z"/></svg>
        +41 76 519 47 83
      </li>
      <li>
        <svg viewBox="0 0 24 24"><rect x="2" y="5" width="20" height="14" rx="2" fill="none" stroke="var(--white)" stroke-width="2"/><path d="M3 6l9 7 9-7" fill="none" stroke="var(--white)" stroke-width="2"/></svg>
        info@varomir-fs.ch
      </li>
      <li>
        <svg viewBox="0 0 24 24" fill="none" stroke="var(--white)" stroke-width="1.8"><circle cx="12" cy="12" r="9.5"/><ellipse cx="12" cy="12" rx="4.5" ry="9.5"/><path d="M2.5 12h19M4 7h16M4 17h16"/></svg>
        <span>www.<strong>varomir-fs</strong>.ch</span>
      </li>
    </ul>
  </div>
</section>

</body>
</html>
```